Banner ads for LP that work with same theme as below banners

Love the banner ads below. Need more with attached photos. But use the same wording, font as in below banner ads. Should be LP size 1200/627 so I can use for Pixorly and LP. Looking for great ads to use as LP ads. We do lots of ads so it will be worth your time to enter this contest you will be rewarded with a ton of work. Need several banner ads that work together. So maybe 1 of the dresses, 1 of the sweater, 1 of the leggings, 1 of the jacket

Target Market(s)

Women 24-45

Industry/Entity Type

Fashion

Requirements
Must have
• Banner ads that work for LP and Pixorly
Nice to have
• Several options to choose from
Should not have
• not sure

```html
<!DOCTYPE html>
<html lang="en">
<head>
<meta charset="utf-8">
<title>Dress for the Occasion – Dresses</title>
<link rel="stylesheet" href="https://fonts.googleapis.com/css2?family=Great+Vibes&family=Playfair+Display:wght@400;700&display=swap">
<style>
  :root {
    --white: #ffffff;
    --mist: #d9dadf;
    --slate: #8c8fa0;
    --dusk: #53576f;
    --navy: #2f3350;
    --navy-deep: #2a2d48;
    --ink: #3a3a3a;
    --dress-blue: #2f6fb3;
    --dress-dark: #2a2226;
    --dress-nude: #d9b9a0;
  }
  * { margin: 0; padding: 0; box-sizing: border-box; }
  html, body { width: 1200px; height: 627px; overflow: hidden; }
  .banner {
    position: relative;
    width: 1200px;
    height: 627px;
    overflow: hidden;
    background: linear-gradient(90deg,
      var(--white) 0%,
      var(--white) 28%,
      var(--mist) 40%,
      var(--slate) 55%,
      var(--dusk) 68%,
      var(--navy) 82%,
      var(--navy-deep) 100%);
  }
  .model-photo {
    position: absolute;
    left: 95px;
    top: 0;
    width: 270px;
    height: 627px;
    background: linear-gradient(180deg,
      var(--dress-nude) 0%,
      var(--dress-dark) 30%,
      var(--dress-blue) 55%,
      var(--dress-dark) 80%,
      var(--dress-nude) 100%);
    opacity: 0.85;
  }
  .offer {
    position: absolute;
    left: 753px;
    top: 228px;
    width: 344px;
    text-align: center;
    color: var(--white);
  }
  .offer-title {
    font-family: "Great Vibes", cursive;
    font-weight: 400;
    font-size: 50px;
    line-height: 1;
    white-space: nowrap;
  }
  .offer-category {
    margin-top: 14px;
    font-family: "Playfair Display", serif;
    font-weight: 700;
    font-size: 19px;
    letter-spacing: 4px;
  }
  .offer-button {
    display: flex;
    align-items: center;
    justify-content: center;
    margin-top: 25px;
    width: 344px;
    height: 73px;
    background: var(--white);
    color: var(--ink);
    font-family: "Playfair Display", serif;
    font-size: 19px;
    letter-spacing: 2px;
    text-decoration: none;
  }
  .offer-button strong { font-weight: 700; }
  .offer-button span { font-weight: 400; margin: 0 0.4em; }
</style>
</head>
<body>
  <main class="banner">
    <div class="model-photo" role="img" aria-label="Model with long wavy hair wearing a long-sleeved blue and black floral lace mini dress with a black waistband"></div>
    <section class="offer">
      <h1 class="offer-title">Dress for the Ocassion</h1>
      <p class="offer-category">-DRESSES-</p>
      <a class="offer-button" href="#"><strong>GET</strong><span>YOURS</span><strong>NOW</strong></a>
    </section>
  </main>
</body>
</html>
```